Business Card Design Project

Business card based on attached logo

Todd Merrick
Todd@lorvantest.com
877-514-9073 ext. 318
Www.LorvanTest.com

Industry/Entity Type

Business

```html
<!DOCTYPE html>
<html lang="en">
<head>
<meta charset="utf-8">
<title>LorvanTest Business Cards</title>
<link rel="stylesheet" href="https://fonts.googleapis.com/css2?family=Arimo:ital,wght@0,400;0,700;1,700&display=swap">
<style>
  :root {
    --stage: #6e4a2e;
    --label: #1a1a1a;
    --card-white: #ffffff;
    --card-grey: #ececec;
    --brand-red: #e31b23;
    --deep-red: #b01e22;
    --ink: #111111;
    --text-grey: #333333;
    --rule-grey: #9a9a9a;
  }
  * { margin: 0; padding: 0; box-sizing: border-box; }
  html, body { width: 1200px; height: 788px; overflow: hidden; }
  body {
    background: var(--stage);
    font-family: "Arimo", Arial, sans-serif;
    position: relative;
  }
  .view-label {
    position: absolute;
    width: 525px;
    text-align: center;
    font-size: 21px;
    color: var(--label);
  }
  .card {
    position: absolute;
    width: 525px;
    height: 300px;
    border-radius: 20px;
    background: var(--card-white);
    overflow: hidden;
  }
  .card--front { left: 54px; top: 74px; }
  .card--back-one { left: 622px; top: 74px; }
  .card--back-two { left: 54px; top: 445px; background: linear-gradient(#c8262a, var(--deep-red)); }
  .card--back-three { left: 622px; top: 445px; background: var(--card-grey); }

  .wordmark {
    position: absolute;
    left: 0; right: 0;
    display: flex;
    justify-content: center;
    align-items: center;
    gap: 10px;
  }
  .wordmark__name {
    font-weight: 700;
    font-size: 52px;
    letter-spacing: -1px;
    color: var(--ink);
    line-height: 1;
  }
  .wordmark__square {
    width: 16px; height: 16px;
    background: var(--brand-red);
    align-self: flex-start;
  }
  .wordmark--on-red .wordmark__square { background: var(--card-white); }
  .wordmark--small .wordmark__name { font-size: 40px; }
  .wordmark--small .wordmark__square { width: 13px; height: 13px; }

  .contact-band {
    position: absolute;
    left: 0; right: 0;
    top: 206px;
    height: 33px;
    background: var(--brand-red);
    border-top: 2px solid var(--card-white);
    border-bottom: 2px solid var(--card-white);
    box-shadow: 0 -3px 0 var(--rule-grey), 0 3px 0 var(--rule-grey);
    color: var(--card-white);
  }
  .contact-band__name {
    position: absolute; left: 54px; top: 5px;
    font-weight: 700; font-size: 17px;
  }
  .contact-band__phone {
    position: absolute; right: 70px; top: 7px;
    font-size: 13px;
  }
  .field-key { font-weight: 700; font-style: italic; }
  .contact-line {
    position: absolute; left: 0; right: 0; top: 261px;
    text-align: center;
    font-size: 13px;
    color: var(--text-grey);
  }
  .contact-line__divider { margin: 0 8px; }
  .web-address {
    position: absolute; left: 0; right: 0; top: 250px;
    text-align: center;
    font-size: 17px;
    color: var(--text-grey);
  }
  .web-address--on-red { color: var(--card-white); }
  .logo-panel {
    position: absolute;
    left: 81px; top: 83px;
    width: 362px; height: 128px;
    background: var(--card-white);
    border: 1px solid #d4d4d4;
  }
</style>
</head>
<body>
  <div class="view-label" style="left:54px; top:34px;">Front</div>
  <div class="view-label" style="left:622px; top:34px;">Back - 1</div>
  <div class="view-label" style="left:54px; top:404px;">Back - 2</div>
  <div class="view-label" style="left:622px; top:404px;">Back - 3</div>

  <section class="card card--front">
    <div class="wordmark" style="top:78px;">
      <span class="wordmark__name">LorvanTest</span>
      <span class="wordmark__square"></span>
    </div>
    <div class="contact-band">
      <span class="contact-band__name">Todd Merrick</span>
      <span class="contact-band__phone"><span class="field-key">phone</span> 877-514-9073 ext. 318</span>
    </div>
    <p class="contact-line">
      <span class="field-key">email</span> Todd@lorvantest.com<span class="contact-line__divider">|</span><span class="field-key">web</span> www.LorvanTest.com
    </p>
  </section>

  <section class="card card--back-one">
    <div class="wordmark" style="top:96px;">
      <span class="wordmark__name">LorvanTest</span>
      <span class="wordmark__square"></span>
    </div>
    <p class="web-address">www.LorvanTest.com</p>
  </section>

  <section class="card card--back-two">
    <div class="wordmark wordmark--on-red" style="top:96px;">
      <span class="wordmark__name">LorvanTest</span>
      <span class="wordmark__square"></span>
    </div>
    <p class="web-address web-address--on-red">www.LorvanTest.com</p>
  </section>

  <section class="card card--back-three">
    <div class="logo-panel">
      <div class="wordmark wordmark--small" style="top:44px;">
        <span class="wordmark__name">LorvanTest</span>
        <span class="wordmark__square"></span>
      </div>
    </div>
    <p class="web-address">www.LorvanTest.com</p>
  </section>
</body>
</html>
```